Web Developer Needs a Business Card Design

I need a personal business card design that represents me as a web developer for potential employers. I would like the background to be a dark color on the front for contrast with my logo and name. The back will have all my information along with a smaller version of the logo. I want something with a modern look and feel, not too conservative. This will be used for potential employers and freelance work.

Industry/Entity Type

Business

Contact Information for Business Card

Front should have my logo and name. The back should have all my personal information which would include: name: Tom Varulek, phone: 570-614-3098, email: tomvarulek@quillbox.net, website url: www.tomvarulek.net, logo, web developer.

Font styles to use
Sans Serif

Requirements
Must have
• Must include my logo. The color palette base color will be the logo color.

```html
<!DOCTYPE html>
<html lang="en">
<head>
<meta charset="utf-8">
<title>Tom Varulek — Business Card</title>
<link rel="stylesheet" href="https://fonts.googleapis.com/css2?family=Roboto:wght@400;500&display=swap">
<style>
  :root {
    --stage: #3b3431;
    --card: #1a1a1b;
    --card-edge: #262627;
    --teal: #5cc3ad;
    --white: #f4f4f4;
  }
  * { margin: 0; padding: 0; box-sizing: border-box; }
  html, body { width: 1200px; height: 780px; overflow: hidden; }
  body {
    background: var(--stage);
    font-family: "Roboto", Arial, sans-serif;
    position: relative;
  }
  .card {
    position: absolute;
    top: 241px;
    width: 520px;
    height: 297px;
    background: var(--card);
    border: 1px solid var(--card-edge);
    border-radius: 3px;
    box-shadow: 0 10px 30px rgba(0,0,0,0.35);
  }
  .card--front { left: 60px; }
  .card--back { left: 620px; }

  .brand {
    position: absolute;
    display: flex;
    align-items: center;
    gap: 10px;
    color: var(--teal);
    font-weight: 500;
    letter-spacing: 0.02em;
  }
  .brand__dot {
    background: var(--teal);
    border-radius: 50%;
    flex: none;
  }
  .card--front .brand { top: 78px; left: 0; right: 0; justify-content: center; font-size: 30px; }
  .card--front .brand__dot { width: 22px; height: 22px; }
  .front-name {
    position: absolute;
    top: 176px;
    left: 0; right: 0;
    text-align: center;
    color: var(--white);
    font-size: 34px;
    font-weight: 400;
    letter-spacing: 0.01em;
  }

  .card--back .brand { top: 134px; left: 36px; font-size: 24px; }
  .card--back .brand__dot { width: 18px; height: 18px; }
  .divider {
    position: absolute;
    left: 236px;
    top: 40px;
    width: 2px;
    height: 220px;
    background: var(--teal);
  }
  .identity { position: absolute; left: 268px; top: 56px; }
  .identity__name { color: var(--teal); font-size: 30px; font-weight: 400; }
  .identity__role { color: var(--white); font-size: 15px; margin-top: 2px; }
  .contacts {
    position: absolute;
    left: 262px;
    top: 170px;
    list-style: none;
  }
  .contacts__item {
    display: flex;
    align-items: center;
    gap: 12px;
    color: var(--white);
    font-size: 17px;
    line-height: 1;
    margin-bottom: 14px;
  }
  .contacts__icon { width: 12px; height: 12px; flex: none; }
</style>
</head>
<body>
  <section class="card card--front" aria-label="Card front">
    <div class="brand"><span class="brand__dot"></span>Varulek</div>
    <h1 class="front-name">TOM VARULEK</h1>
  </section>

  <section class="card card--back" aria-label="Card back">
    <div class="brand"><span class="brand__dot"></span>Varulek</div>
    <div class="divider"></div>
    <div class="identity">
      <h2 class="identity__name">Tom Varulek</h2>
      <p class="identity__role">web developer</p>
    </div>
    <ul class="contacts">
      <li class="contacts__item">
        <svg class="contacts__icon" viewBox="0 0 12 12"><rect width="12" height="12" rx="2" fill="#5cc3ad"/><path d="M4 3.2c-.4.2-.8.8-.6 1.6.4 1.7 1.9 3.3 3.7 3.8.8.2 1.3-.2 1.5-.6L7.5 7l-.8.5C5.9 7.1 5.2 6.4 4.8 5.6l.5-.8z" fill="#1a1a1b"/></svg>
        570-614-3098
      </li>
      <li class="contacts__item">
        <svg class="contacts__icon" viewBox="0 0 12 12"><rect width="12" height="12" rx="2" fill="#5cc3ad"/><rect x="2.5" y="3.5" width="7" height="5" fill="#1a1a1b"/><path d="M2.5 3.5L6 6.3l3.5-2.8" stroke="#5cc3ad" stroke-width="0.8" fill="none"/></svg>
        tomvarulek@quillbox.net
      </li>
      <li class="contacts__item">
        <svg class="contacts__icon" viewBox="0 0 12 12"><rect width="12" height="12" rx="2" fill="#5cc3ad"/><circle cx="6" cy="6" r="3.3" fill="none" stroke="#1a1a1b" stroke-width="0.9"/><path d="M2.7 6h6.6M6 2.7c-1.4 1.8-1.4 4.8 0 6.6M6 2.7c1.4 1.8 1.4 4.8 0 6.6" stroke="#1a1a1b" stroke-width="0.7" fill="none"/></svg>
        www.tomvarulek.net
      </li>
    </ul>
  </section>
</body>
</html>
```